Business Card - connecting 2 souls and beggining the journey of self discovery

Logo on the front
with tag line

On the back list of services and contact details

Seminars
workshops
Coaching
podcasts

Darren Whitlow
Health & Wellbeing Life Coach
0491 372 615
darren@brightcoreliving.example
brightcoreliving.example

Industry/Entity Type

Life Coaching

Contact Information for Business Card

I like the use of colour from the logo to be used. I'm not a fan of white.

Requirements
Must have
• My tagline: The journey home starts with you
Nice to have
• Use of colour that is in the Brightcore Living logo

```html
<!DOCTYPE html>
<html lang="en">
<head>
<meta charset="utf-8">
<title>Darren Whitlow – Business Card</title>
<link href="https://fonts.googleapis.com/css2?family=Montserrat:wght@500;600&family=Quicksand:wght@500;600;700&family=Cherry+Swash:wght@700&display=swap" rel="stylesheet">
<style>
  :root {
    --stage: #1b1c20;
    --paper: #f4f4f4;
    --ink: #1a1a1a;
    --coral: #ef6670;
    --black: #050505;
    --slate: #3f4450;
    --white: #ffffff;
  }
  * { box-sizing: border-box; margin: 0; padding: 0; }
  html, body { width: 1200px; height: 1200px; overflow: hidden; background: var(--stage); }
  .stage { position: relative; width: 1200px; height: 1200px; }

  .card { position: absolute; left: 120px; width: 960px; height: 549px; overflow: hidden; }
  .card--info { top: 34px; background: var(--paper); }
  .card--brand { top: 617px; background: var(--slate); }

  .band { position: absolute; }
  .band--coral { background: var(--coral); }
  .band--black { background: var(--black); }

  .brand-mark { position: absolute; display: flex; align-items: center; gap: 14px; }
  .brand-dot { border-radius: 50%; background: var(--coral); flex: none; }
  .brand-name { font-family: "Quicksand", sans-serif; font-weight: 700; white-space: nowrap; }

  .card--info .brand-mark { left: 0; width: 440px; top: 46px; justify-content: center; }
  .card--info .brand-dot { width: 56px; height: 56px; }
  .card--info .brand-name { font-size: 27px; color: var(--ink); }

  .tagline { position: absolute; font-family: "Cherry Swash", serif; font-weight: 700; white-space: nowrap; }
  .card--info .tagline { left: 0; width: 440px; text-align: center; top: 140px; font-size: 20px; color: var(--ink); }

  .services { position: absolute; left: 142px; top: 230px; list-style: none; font-family: "Quicksand", sans-serif; font-weight: 500; font-size: 30px; color: var(--coral); }
  .services li { height: 56px; position: relative; padding-left: 20px; }
  .services li::before { content: ""; position: absolute; left: 0; top: 20px; width: 8px; height: 8px; border-radius: 50%; background: var(--ink); }

  .person { position: absolute; left: 472px; top: 74px; }
  .person-name { font-family: "Montserrat", sans-serif; font-weight: 600; font-size: 38px; letter-spacing: -0.5px; color: var(--ink); line-height: 1; }
  .person-name .surname { color: var(--coral); }
  .person-role { font-family: "Montserrat", sans-serif; font-weight: 500; font-size: 20px; color: var(--ink); margin-top: 6px; }

  .contact { position: absolute; left: 418px; width: 542px; height: 104px; display: flex; align-items: center; padding-left: 58px; gap: 32px; font-family: "Quicksand", sans-serif; font-weight: 700; color: var(--white); }
  .contact-icon { width: 54px; height: 54px; border-radius: 50%; background: var(--white); display: flex; align-items: center; justify-content: center; flex: none; }
  .contact--phone { top: 190px; background: var(--coral); font-size: 22px; }
  .contact--mail { top: 294px; background: var(--black); font-size: 20px; }
  .contact--web { top: 398px; background: var(--coral); font-size: 20px; font-weight: 500; }

  .card--brand .brand-mark { left: 0; width: 960px; top: 222px; justify-content: center; gap: 20px; }
  .card--brand .brand-dot { width: 76px; height: 76px; }
  .card--brand .brand-name { font-size: 44px; color: var(--white); }
  .card--brand .tagline { left: 0; width: 960px; text-align: center; top: 380px; font-size: 37px; color: var(--white); }
</style>
</head>
<body>
<main class="stage">

  <section class="card card--info" aria-label="Card back: services and contact details">
    <div class="band band--coral" style="left:0;top:190px;width:40px;height:104px"></div>
    <div class="band band--black" style="left:0;top:294px;width:40px;height:104px"></div>
    <div class="band band--coral" style="left:0;top:398px;width:40px;height:104px"></div>

    <div class="brand-mark">
      <span class="brand-dot"></span>
      <span class="brand-name">Brightcore Living</span>
    </div>
    <p class="tagline">The journey home starts with you</p>

    <ul class="services">
      <li>Seminars</li>
      <li>Workshops</li>
      <li>Coaching</li>
      <li>Podcasts</li>
    </ul>

    <div class="person">
      <h1 class="person-name">DARREN <span class="surname">WHITLOW</span></h1>
      <p class="person-role">HEALTH &amp; WELLBEING LIFE COACH</p>
    </div>

    <div class="contact contact--phone">
      <span class="contact-icon">
        <svg width="20" height="28" viewBox="0 0 20 28" aria-hidden="true"><rect x="3" y="1" width="14" height="26" rx="3" fill="#1a1a1a"/><rect x="6" y="5" width="8" height="15" fill="#fff"/><circle cx="10" cy="23.5" r="1.5" fill="#fff"/></svg>
      </span>
      <span>0491 372 615</span>
    </div>
    <div class="contact contact--mail">
      <span class="contact-icon">
        <svg width="26" height="20" viewBox="0 0 26 20" aria-hidden="true"><rect x="1" y="2" width="24" height="16" rx="2" fill="#1a1a1a"/><path d="M2 4 L13 12 L24 4" fill="none" stroke="#fff" stroke-width="2"/></svg>
      </span>
      <span>darren@brightcoreliving.example</span>
    </div>
    <div class="contact contact--web">
      <span class="contact-icon">
        <svg width="32" height="32" viewBox="0 0 32 32" aria-hidden="true" fill="none" stroke="#1a1a1a" stroke-width="2"><circle cx="16" cy="16" r="13"/><ellipse cx="16" cy="16" rx="6" ry="13"/><line x1="16" y1="3" x2="16" y2="29"/><line x1="3" y1="16" x2="29" y2="16"/><path d="M5.5 9 H26.5 M5.5 23 H26.5"/></svg>
      </span>
      <span>www.brightcoreliving.example</span>
    </div>
  </section>

  <section class="card card--brand" aria-label="Card front: name and tagline">
    <div class="band" style="left:0;top:0;width:40px;height:549px;background:var(--paper)"></div>
    <div class="band band--coral" style="left:0;top:190px;width:40px;height:104px"></div>
    <div class="band band--black" style="left:0;top:294px;width:40px;height:104px"></div>
    <div class="band band--coral" style="left:0;top:398px;width:40px;height:104px"></div>

    <div class="band" style="left:927px;top:0;width:33px;height:549px;background:var(--paper)"></div>
    <div class="band band--coral" style="left:927px;top:190px;width:33px;height:104px"></div>
    <div class="band band--black" style="left:927px;top:294px;width:33px;height:104px"></div>
    <div class="band band--coral" style="left:927px;top:398px;width:33px;height:104px"></div>

    <div class="brand-mark">
      <span class="brand-dot"></span>
      <span class="brand-name">Brightcore Living</span>
    </div>
    <p class="tagline">The journey home starts with you</p>
  </section>

</main>
</body>
</html>
```